Dietary supplement, Clean and simple.

Hi,
I’d like to talk about the project,

About us:
We are a dietary supplement (Vitamins, Minerals, amino acids etc.) company.
The goal is to have about 25 products at the end of this year. However, for this goal to be achieved we need a good label design to make our products represent our company values.
I’ll be here every day supporting your questions, we are fully committed to making the highest/best quality/customer experience possible.

About the design and our values:
- Professional (We are in the industry of professionalism and expertise. I would love to show we are competent at this, Id. Like to have the labels looks like we have done our research.)
- Efficient (White spacing, good use of the space available.)
- Simple (Straight forward, in 5 seconds they have to know what the product they have is/how functions. We’re trying to simplify it for the consumer.
- No distractions (the only visually “distracting” factor can be the vector art.)

The guidelines:
The goal is to have a universal design, with one element that changes (Vector art). I’ll attach a file/multiple files I think can show some visuals on what I’m looking for, and what parts of the design I think are good/bad.

Label size: 69x155mm (Front is 77.5mm)

Design whatever you think fits our image. You’re the design expert, all I care about is that it fits our company standards/image.

Use this color/font.
Font: Sans Serif
Main company color is Mind green #237D62 (Use this color for something in the design.)

What I thought would be cool/might looks ugly, who knows:
1. The front of the label: Should have 1 vector art, preferably in the top right corner. (That looks good in multiple colors. The vector can have multiple areas to color, I would prefer 2 main colors in the vector art. The interchangeable colors are used for multiple kinds of products.)
2. Text/product information on the left. The text that will have to be displayed:
- Product name for instance “Magnesium + B6”
- Description for the product for instance “Magnesium with ginger taste”
- Company name or logo. (Add ® behind it. We are soon to be trademark registered.)
3. We need to show the "daily intake" amount on the front and also the amount in the complete bottle. For instance, “Daily intake 1 capsule, 60 capsules”.
• You don’t have to design the backside of the label. After I chose a design, I’d like to chat and give specific information on what areas need to be assigned where. (Too complex because of the law.)
Updates

Hi, Please make the deadline 31 days total. I want designers to have the time to design. And not be rushed to finish it.

I want to extend the deadline because i feel like a slightly more medical look would be interesting. Hope you can come up with something!!

Target Market(s)

Dietary supplement consumers

Industry/Entity Type

Dietary supplements

Font styles to use
Sans Serif

Colors

Designer to choose colors to be used in the design.

Requirements
Must have
• Trademark icon "®" has to be at the top right after the company logo(text of logo)/name.

```html
<!DOCTYPE html>
<html lang="en">
<head>
<meta charset="utf-8">
<title>Verdant Calm — Magnesium + B6 Label</title>
<link rel="stylesheet" href="https://fonts.googleapis.com/css2?family=Josefin+Sans:wght@300;400&family=Montserrat:wght@300;400;700&display=swap">
<style>
  :root {
    --canvas-bg: #ffffff;
    --label-light: #ececec;
    --label-mid: #dedede;
    --label-band: #d3d3d3;
    --brand-green: #0d5a1f;
    --ink: #111111;
    --muted: #8a8a8a;
    --art-a: #4f9a63;
    --art-b: #a6d66f;
  }
  * { margin: 0; padding: 0; box-sizing: border-box; }
  html, body {
    width: 1200px;
    height: 873px;
    overflow: hidden;
    background: var(--canvas-bg);
  }
  .canvas {
    position: relative;
    width: 1200px;
    height: 873px;
    display: flex;
    align-items: center;
    justify-content: center;
  }
  .label {
    position: relative;
    width: 600px;
    height: 700px;
    background: linear-gradient(180deg, var(--label-light) 0%, var(--label-mid) 44%, var(--label-band) 44%, var(--label-band) 100%);
    display: flex;
    flex-direction: column;
    align-items: center;
  }
  .brand {
    margin-top: 120px;
    display: flex;
    align-items: center;
    gap: 14px;
    color: var(--brand-green);
    font-family: "Montserrat", sans-serif;
    font-weight: 700;
    font-size: 44px;
    letter-spacing: 2px;
    line-height: 1;
  }
  .brand-dot {
    width: 18px;
    height: 18px;
    border-radius: 50%;
    background: var(--brand-green);
  }
  .brand-name sup {
    font-size: 16px;
    vertical-align: top;
    margin-left: 4px;
    position: relative;
    top: -6px;
  }
  .art-slot {
    margin-top: 66px;
    width: 160px;
    height: 110px;
    background: linear-gradient(135deg, var(--art-a), var(--art-b));
    opacity: 0.85;
  }
  .product-name {
    margin-top: 56px;
    font-family: "Josefin Sans", sans-serif;
    font-weight: 300;
    font-size: 54px;
    color: var(--ink);
    letter-spacing: 1px;
    line-height: 1;
    white-space: nowrap;
  }
  .product-name .plus { font-size: 40px; margin: 0 8px; }
  .product-desc {
    margin-top: 10px;
    font-family: "Montserrat", sans-serif;
    font-weight: 300;
    font-size: 14px;
    letter-spacing: 3px;
    color: var(--muted);
    text-transform: uppercase;
  }
  .dosage {
    margin-top: 70px;
    display: flex;
    align-items: center;
    gap: 24px;
    font-family: "Montserrat", sans-serif;
    font-size: 12.5px;
    letter-spacing: 1px;
    text-transform: uppercase;
    color: var(--muted);
    font-weight: 300;
  }
  .dosage strong { color: var(--ink); font-weight: 700; }
  .dosage-sep {
    width: 6px;
    height: 6px;
    border-radius: 50%;
    background: var(--ink);
  }
</style>
</head>
<body>
<main class="canvas">
  <section class="label">
    <div class="brand">
      <span class="brand-dot"></span>
      <span class="brand-name">VERDANT CALM<sup>®</sup></span>
    </div>

    <div class="art-slot" role="img" aria-label="Interchangeable product vector artwork in green tones"></div>

    <h1 class="product-name">MAGNESIUM<span class="plus">+</span>B6</h1>
    <p class="product-desc">Magnesium with ginger taste</p>

    <div class="dosage">
      <span><strong>60</strong> Capsules</span>
      <span class="dosage-sep"></span>
      <span><strong>1 Capsule</strong> Daily intake</span>
    </div>
  </section>
</main>
</body>
</html>
```